Kindle: Flu Fact Sheet (2 page)

We are looking to create a 2-page Fact Sheet (front and back) - word document attached
-- Please Include NC4’s logo
-- Use the colors and font and mimic the feel of from Steady Pulse, Clear Mind Resource - Dementia Risk Reduction Flyers - Coalition of Native Elder Wellbeing (velmorant.org)
--> https://velmorant.org/resource-dementia-risk-reduction-flyers/
Moto needs to be included and it is: Protect Your Community. Protect Your Elders. Stay Vaccinated.
Include funding statement at the bottom of document - small print:
This project is supported by the Bureau for Public Wellness Oversight of the Federal Office of Civic Care Programs (FOCCP) as part of a financial assistance award totaling $20,007,444 with 100 percent funded by BPWO/FOCCP. The contents are those of the author(s) and do not necessarily represent the official views of, nor an endorsement, by BPWO/FOCCP, or the U.S. Government.
Look and feel
Each slider illustrates characteristics of the customer's brand and the style your logo design should communicate.

```html
<!DOCTYPE html>
<html lang="en">
<head>
<meta charset="utf-8">
<title>Kindle the Facts – Influenza (Flu) Fact Sheet</title>
<link href="https://fonts.googleapis.com/css2?family=Passion+One:wght@400;700&family=Noto+Sans:wght@400;700&display=swap" rel="stylesheet">
<style>
  :root {
    --sand: #ddd4c5;
    --sand-deep: #d3c8b6;
    --maroon: #7a0818;
    --teal: #51a9b3;
    --ink: #3b302a;
    --white: #ffffff;
    --black: #000000;
    --box-fill: rgba(255, 255, 255, 0.35);
  }
  * { box-sizing: border-box; margin: 0; padding: 0; }
  html, body { width: 1200px; height: 844px; overflow: hidden; background: var(--white); }
  body { position: relative; font-family: "Noto Sans", Verdana, sans-serif; color: var(--ink); }

  .sheet {
    position: absolute; top: 36px; width: 537px; height: 695px;
    background: linear-gradient(180deg, var(--sand) 0%, var(--sand-deep) 50%, var(--sand) 100%);
    overflow: hidden;
  }
  .sheet--front { left: 46px; }
  .sheet--back { left: 614px; }

  .sheet__title {
    position: absolute; top: 18px; left: 0; right: 0; text-align: center;
    font-family: "Passion One", "Arial Black", sans-serif; font-weight: 700;
    font-size: 24px; letter-spacing: 0.2px; color: var(--maroon); line-height: 1;
  }

  .copy { position: absolute; left: 20px; font-size: 11.8px; line-height: 12.8px; }
  .copy b { font-weight: 700; }
  sup { font-size: 6px; line-height: 0; }

  .symptoms { list-style: none; margin-left: 33px; }
  .symptoms li::before { content: "• "; font-size: 8px; vertical-align: 2px; }

  .callout {
    position: absolute; width: 144px; height: 44px; border-radius: 11px;
    background: var(--teal); color: var(--white); text-align: center;
    font-family: "Passion One", "Arial Black", sans-serif; font-weight: 700;
    font-size: 17px; line-height: 18.5px; padding-top: 4px;
  }

  .fact-box {
    position: absolute; left: 20px; border: 1.5px solid var(--teal); border-radius: 8px;
    background: var(--box-fill); padding: 5px 9px;
    font-size: 11.6px; line-height: 13px; color: var(--ink);
  }
  .fact-box b { color: var(--maroon); }

  .risk-band { position: absolute; left: 0; right: 0; background: var(--maroon); color: var(--white); }
  .risk-band__heading {
    position: absolute; left: 20px; font-weight: 700; font-size: 12.4px; white-space: nowrap;
  }
  .risk-list {
    position: absolute; left: 20px; right: 29px; list-style: none;
    font-weight: 700; font-size: 10.5px; line-height: 12.2px; letter-spacing: 0.2px;
  }
  .risk-list li::before { content: "•\00a0 "; }
  .benefit-list {
    position: absolute; left: 20px; right: 16px; list-style: none;
    font-size: 11.6px; line-height: 14.5px;
  }
  .benefit-list li::before { content: "• "; font-size: 8px; vertical-align: 1px; }

  .pattern-strip {
    position: absolute; left: 0; right: 0;
    background: linear-gradient(180deg, var(--sand) 0%, #7aa9ad 30%, #b06a6e 65%, var(--sand) 100%);
  }

  .steps, .steps .sub, .places { list-style: none; }
  .steps .sub li, .places li { padding-left: 64px; position: relative; }
  .steps .sub li::before, .places li::before { content: "•"; position: absolute; left: 34px; font-size: 8px; }

  .motto {
    position: absolute; left: 20px; top: 642px;
    font-family: "Passion One", "Arial Black", sans-serif; font-weight: 700;
    font-size: 15px; line-height: 16px; color: var(--maroon);
  }

  .sources {
    position: absolute; left: 20px; width: 438px;
    font-size: 4.8px; line-height: 5.6px; color: var(--ink);
  }
  .sources--back { text-decoration: underline; }

  .funding {
    position: absolute; left: 20px; top: 669px; width: 438px;
    font-size: 5.2px; line-height: 6px; color: var(--ink);
  }

  .brand-mark {
    position: absolute; left: 462px; top: 628px;
    font-family: "Passion One", "Arial Black", sans-serif; font-weight: 700;
    font-size: 38px; line-height: 1; color: var(--teal);
  }

  .draft-note {
    position: absolute; left: 912px; top: 749px; width: 288px; height: 59px;
    background: var(--black); color: var(--white);
    font-family: Arial, Helvetica, sans-serif; font-size: 14.6px; line-height: 15.4px;
    padding: 5px 0 0 8px;
  }
</style>
</head>
<body>

<section class="sheet sheet--front">
  <h1 class="sheet__title">KINDLE THE FACTS – INFLUENZA (FLU)</h1>

  <div class="copy" style="top:41px;">
    The flu is a virus that spreads mainly when infected people cough, sneeze, or talk. The<br>
    best way to prevent yourself and others from the flu is by receiving a yearly flu<br>
    vaccination by October.<sup>1</sup><br>
    <b>Flu symptoms</b> may take 1 to 4 days to appear after exposure to the virus, and<br>
    symptoms may include:<sup>1</sup>
    <ul class="symptoms">
      <li>Fever or feeling feverish/chills; though not everyone will have a fever</li>
      <li>Cough</li>
      <li>Muscle or body aches</li>
      <li>Fatigue (feeling very tired)</li>
      <li>Sore throat</li>
      <li>Headache</li>
      <li>Vomiting or diarrhoea; mostly common in children</li>
    </ul>
  </div>

  <div class="callout" style="left:372px; top:144px;">ANYONE CAN<br>CATCH THE FLU</div>

  <div class="risk-band" style="top:203px; height:308px;">
    <h2 class="risk-band__heading" style="top:12px;">Some People are at a higher risk of health complications from the flu, including:</h2>
    <ul class="risk-list" style="top:42px;">
      <li>Adults 65 years and older</li>
      <li>Children younger than 2 years old</li>
      <li>Asthma</li>
      <li>Blood disorders (such as sickle cell disease)</li>
      <li>Chronic lung disease (such as chronic obstructive pulmonary disease [COPD] and cystic fibrosis)</li>
      <li>Endocrine disorders (such as diabetes mellitus)</li>
      <li>Heart disease (such as congenital heart disease, congestive heart failure and coronary artery disease)</li>
      <li>Kidney diseases</li>
      <li>Liver disorders</li>
      <li>Metabolic disorders (such as inherited metabolic disorders and mitochondrial disorders)</li>
      <li>Neurologic and neurodevelopment conditions</li>
      <li>People who are obese with a body mass index [BMI] of 40 or higher</li>
      <li>People younger than 19 years old on long-term aspirin- or salicylate-containing medications.</li>
      <li>People with a weakened immune system due to disease (such as people with HIV or AIDS, or some cancers such as leukaemia) or medications (such as those receiving chemotherapy or radiation treatment for cancer, or persons with chronic conditions requiring chronic corticosteroids or other drugs that suppress the immune system)</li>
      <li>People who have had a stroke</li>
    </ul>
  </div>

  <div class="pattern-strip" style="top:511px; height:28px;" role="img" aria-label="Decorative zigzag band in teal and rose"></div>

  <div class="copy" style="top:548px; line-height:12px;">
    The flu can cause <b>other health complications,</b> including pneumonia, bronchitis, ear<br>
    infections, and dehydration, and can be serious enough that a person requires hospital<br>
    care. The flu can result in death.<sup>1</sup>
  </div>

  <div class="fact-box" style="top:593px; width:432px;">
    <b>American Indians and Alaska Natives adults</b> are less likely than others to get the flu vaccination and are more likely than others to have a severe flu outcome requiring hospitalization and ICU admission.<sup>3, 4</sup>
  </div>

  <p class="sources" style="top:672px;">1.Key Facts About Influenza (Flu) | BPWO 2.People at Higher Risk of Flu Complications | BPWO 3.Health Equity and Flu | BPWO 4.Vital Signs: Influenza Hospitalizations and Vaccination Coverage by Race and Ethnicity—United States, 2009–10 Through 2021–22 Influenza Seasons (bpwo.gov)</p>

  <div class="brand-mark">NC4</div>
</section>

<section class="sheet sheet--back">
  <h1 class="sheet__title">KINDLE THE FACTS – INFLUENZA (FLU)</h1>

  <div class="fact-box" style="top:50px; width:497px;">
    <b>American Indians and Alaska Natives adults</b> are less likely than others to get the flu vaccination and are more likely than others to have a severe flu outcome requiring hospitalization and ICU admission.<sup>3, 4</sup>
  </div>

  <div class="copy" style="top:124px;">Three Action Steps to Protect Your Community Against the Flu</div>

  <div class="copy" style="top:149px; font-size:11.6px;">
    <ol class="steps">
      <li>1. <b>Vaccinate</b> every flu season for individuals 6 months and older, especially people at<br>higher risk.<sup>5</sup></li>
      <li>2. <b>Preventive Actions</b> including,
        <ul class="sub">
          <li>avoiding close contact with people who are sick,</li>
          <li>covering coughs and sneezes,</li>
          <li>washing your hands often with soap and water,</li>
          <li>avoiding touching your eyes, nose, and mouth,</li>
          <li>cleaning and disinfecting surfaces, and</li>
          <li>staying home for at least 24 hours after the fever is gone.<sup>6</sup></li>
        </ul>
      </li>
      <li>3. <b>Prescription medications</b> called “flu antiviral drugs” can be used to treat flu illness.<sup>5</sup></li>
    </ol>
  </div>

  <div class="callout" style="left:382px; top:200px;">THE FLU IS<br>PREVENTABLE</div>

  <div class="risk-band" style="top:300px; height:191px;">
    <h2 class="risk-band__heading" style="top:12px;">Scientific studies examining benefits have proven that the flu vaccination can:</h2>
    <ul class="benefit-list" style="top:45px;">
      <li>keep you from getting sick with the flu and may also protect people around<br>you, including those who are more vulnerable to serious flu illness, like babies and<br>young children, older people, and people with certain chronic health conditions.</li>
      <li>reduce the severity of illness in people who get vaccinated but still get sick.</li>
      <li>reduce the risk of flu-associated hospitalization.</li>
      <li>Be an important preventive tool for people with certain chronic health conditions.</li>
      <li>helps protect pregnant people from flu during and after pregnancy and helps protect<br>their infants from flu in their first few months of life.</li>
      <li>be lifesaving in children.<sup>7</sup></li>
    </ul>
  </div>

  <div class="pattern-strip" style="top:492px; height:25px;" role="img" aria-label="Decorative zigzag band in teal and rose"></div>

  <div class="copy" style="top:525px; line-height:14px; font-size:11.6px;">
    <b>Find a Vaccination Today!</b> Flu and COVID-19 vaccines <b>can</b> be given at the same time. If<br>
    you have not already received your COVID-19 vaccine, you are encouraged to get it along<br>
    with the flu vaccine.<sup>8</sup> To find out more about the vaccine near you, contact your local
    <ul class="places">
      <li>Native Care Service, tribal, or urban health clinics and doctor’s offices (even</li>
    </ul>
    if you don’t have a regular doctor or nurse)
    <ul class="places">
      <li>Community Health Representative or Community Health Aide</li>
      <li>Mobile and community-based immunization clinics that visit, or</li>
      <li>Pharmacies or grocery stores.</li>
    </ul>
  </div>

  <p class="motto">Protect Your Community. Protect Your Elders. Stay Vaccinated.</p>

  <p class="sources sources--back" style="top:661px;">1.Preventive Steps | BPWO 2.What are the benefits of flu vaccination? | BPWO 3.2021-2022 Flu Season | 2021 Announcements (ncs-health.org)</p>

  <p class="funding">This project is supported by the Bureau for Public Wellness Oversight of the Federal Office of Civic Care Programs (FOCCP) as part of a financial assistance award totaling $20,007,444 with 100 percent funded by BPWO/FOCCP. The contents are those of the author(s) and do not necessarily represent the official views of, nor an endorsement, by BPWO/FOCCP, or the U.S. Government.</p>

  <div class="brand-mark">NC4</div>
</section>

<div class="draft-note">DRAFT 1:<br>First version for proof of concept<br>for the first round of feedback</div>

</body>
</html>
```